Corporate Travel Technology Company needs new Business Card design

We need a new business card design to reflect our re-branded company. Our company is called tolvEn (pronounced tolvenn) and we provide Business Intelligence and mobile travel management solutions for the corporate travel industry. Our multinational customers use our solutions to manage large travel budgets and frequent travellers, as well as to save money and reduce risk. We'd like to see designs that use the blue and green palette as well as our corporate logo (attached below). The design should communicate innovation, insight, forward thinking, contemporary, trusted.

Target Market(s)

Large multinational corporates and Travel Agencies.

Industry/Entity Type

Business

Contact Information for Business Card

Rosalind Mercer
Chief Executive
tolvEn
Phone number - +61 (0)2 8134 2907
Email address - rosalind.mercer@tolven-example.com
Mobile number - +61 (0)438 516 702
www.tolven-example.com

Font styles to use
Other font styles liked:
• Please use font as close to corporate logo as possible

Colors
0255a3
0393ce
00a990
33b8a4
33a6d7
3176b5

Requirements
Must have
• Please include the words;
• Mobile Travel Management
• Accelerating Travel Business Insights
• Use corporate logo - although icon can be stylised if needed

```html
<!DOCTYPE html>
<html lang="en">
<head>
<meta charset="utf-8">
<title>tolvEn business card</title>
<link rel="stylesheet" href="https://fonts.googleapis.com/css2?family=Open+Sans:ital,wght@0,400;0,600;1,400&display=swap">
<style>
  :root {
    --backdrop: #8c8c8c;
    --card: #ffffff;
    --brand-blue: #00aeef;
    --brand-slate: #455e5c;
    --ink: #3c3c3c;
    --rule: #555555;
  }
  * { box-sizing: border-box; margin: 0; padding: 0; }
  html, body { width: 1105px; height: 1200px; overflow: hidden; }
  body {
    background: var(--backdrop);
    font-family: "Open Sans", Arial, sans-serif;
    color: var(--ink);
    position: relative;
  }
  .card {
    position: absolute;
    left: 182px;
    width: 747px;
    height: 428px;
    background: var(--card);
    overflow: hidden;
  }
  .card--front { top: 119px; }
  .card--back { top: 635px; }

  .side-panel {
    position: absolute;
    top: 0; right: 0;
    width: 301px; height: 100%;
    background: var(--brand-slate);
  }
  .side-panel__edge {
    position: absolute;
    top: 0; left: 0;
    width: 34px; height: 100%;
    background: var(--brand-blue);
  }

  .identity { position: absolute; left: 43px; top: 68px; }
  .identity__name {
    font-weight: 600;
    font-size: 33px;
    line-height: 1.1;
    color: var(--brand-blue);
  }
  .identity__role {
    font-size: 25px;
    line-height: 1.3;
    color: var(--ink);
  }
  .dotted-rule {
    position: absolute;
    left: 43px;
    width: 320px;
    border-top: 2px dotted var(--rule);
  }
  .dotted-rule--top { top: 156px; }
  .dotted-rule--bottom { top: 297px; }

  .contact-list {
    position: absolute;
    left: 43px; top: 168px;
    list-style: none;
  }
  .contact-list li {
    display: flex;
    align-items: center;
    height: 29px;
    font-size: 18px;
  }
  .contact-list svg { width: 18px; height: 18px; margin-right: 12px; flex: none; }

  .tagline-list {
    position: absolute;
    left: 43px; top: 315px;
    list-style: none;
  }
  .tagline-list li {
    display: flex;
    align-items: center;
    height: 27px;
    font-size: 19px;
    font-style: italic;
  }
  .tagline-list li::before {
    content: "";
    width: 7px; height: 7px;
    border-radius: 50%;
    background: var(--brand-blue);
    margin-right: 13px;
  }

  .wordmark {
    position: absolute;
    left: 0; right: 0; top: 160px;
    display: flex;
    justify-content: center;
    align-items: center;
    gap: 14px;
  }
  .wordmark__name {
    font-size: 88px;
    font-weight: 400;
    line-height: 1;
    color: var(--brand-slate);
  }
  .wordmark__dot {
    width: 26px; height: 26px;
    border-radius: 50%;
    background: var(--brand-blue);
    margin-top: 30px;
  }
</style>
</head>
<body>
  <section class="card card--front">
    <div class="side-panel"><div class="side-panel__edge"></div></div>

    <div class="identity">
      <p class="identity__name">Rosalind Mercer</p>
      <p class="identity__role">Chief Executive</p>
    </div>

    <div class="dotted-rule dotted-rule--top"></div>

    <ul class="contact-list">
      <li>
        <svg viewBox="0 0 20 20" aria-hidden="true"><path fill="#00aeef" d="M4 2l4 0 1.5 4-2.3 1.6a10 10 0 0 0 5.2 5.2L14 10.5l4 1.5v4a2 2 0 0 1-2 2A15 15 0 0 1 2 4a2 2 0 0 1 2-2z"/></svg>
        +61 (0)2 8134 2907
      </li>
      <li>
        <svg viewBox="0 0 20 20" aria-hidden="true"><rect x="5" y="1" width="10" height="18" rx="2" fill="#00aeef"/><rect x="7" y="4" width="6" height="10" fill="#fff"/></svg>
        +61 (0)438 516 702
      </li>
      <li>
        <svg viewBox="0 0 20 20" aria-hidden="true"><rect x="2" y="5" width="16" height="11" fill="#00aeef"/><path d="M2.5 5.5L10 11l7.5-5.5" fill="none" stroke="#fff" stroke-width="1.4"/></svg>
        rosalind.mercer@tolven-example.com
      </li>
      <li>
        <svg viewBox="0 0 20 20" aria-hidden="true"><circle cx="10" cy="10" r="8" fill="#00aeef"/><path d="M2 10h16M10 2c-3 3-3 13 0 16M10 2c3 3 3 13 0 16" fill="none" stroke="#fff" stroke-width="1.2"/></svg>
        www.tolven-example.com
      </li>
    </ul>

    <div class="dotted-rule dotted-rule--bottom"></div>

    <ul class="tagline-list">
      <li>Mobile Travel Management</li>
      <li>Accelerating Travel Business Insights</li>
    </ul>
  </section>

  <section class="card card--back">
    <div class="wordmark">
      <span class="wordmark__name">tolvEn</span>
      <span class="wordmark__dot"></span>
    </div>
  </section>
</body>
</html>
```